Company or website name
- Quiet Hollow Properties
- Describe your company and organization and target audience
- We sell rural vacant, mostly residential land. Our target market is looking for privacy and either a place to retire to or a place to escape to.
- The design should have the following
- Mountains, Pine Trees, Earthy Colors, and match the attached logo. The home page should have designs for slides of properties at the top, followed by a survey (for users to share details of the property they're looking for), followed by search functionality, individual properties and general areas properties are available in. We'll also need at least one contact form on each page as well as maps. For the property detail page we'll need a large area for pictures, highlighted property details, a description and more detailed facts about property. The property detail page should also have a survey for users to share details of what they're looking for and contact form. Last but not least, similar properties should also be included on the property listing page. The winning design will include an excellent "Contact Us" page! Every page should have an opt-in offering users to be notified when new properties become available.
- Briefly describe your contest

```html
<!DOCTYPE html>
<html lang="en">
<head>
<meta charset="utf-8">
<title>Quiet Hollow Properties – Home and Property Detail</title>
<link href="https://fonts.googleapis.com/css2?family=Montserrat:wght@400;500;600;700;800&display=swap" rel="stylesheet">
<style>
:root{
  --green:#8cab50;
  --blue:#1296de;
  --sky-top:#e9f1f8;
  --sky-mid:#7fb3e6;
  --sky-deep:#1676dc;
  --navy:#1b2748;
  --ink:#363636;
  --muted:#5a5a5a;
  --panel:#f2f2f2;
  --white:#ffffff;
  --footer:#3c4442;
  --map-block:#e4e3dc;
}
*{box-sizing:border-box;margin:0;padding:0}
html,body{width:829px;height:1200px;overflow:hidden;background:var(--white)}
body{position:relative;font-family:'Montserrat',sans-serif;color:var(--ink)}
.page{position:absolute;width:349px;overflow:hidden;background:var(--white);box-shadow:0 0 4px rgba(0,0,0,.14)}
.home{left:43px;top:44px;height:1008px}
.detail{left:437px;top:44px;height:1109px}
.abs{position:absolute}
.section{position:absolute;left:0;width:349px}
.panel{background:var(--panel)}

/* navigation + brand */
.nav{position:absolute;top:9px;left:226px;display:flex;gap:7px;font-size:3.3px;letter-spacing:.2px;color:var(--muted);font-weight:500}
.brand{position:absolute;left:30px;top:8px;display:flex;align-items:center;gap:3px;width:60px}
.brand-dot{width:13px;height:13px;border-radius:50%;background:var(--navy);flex:none}
.brand-name{font-size:5.4px;font-weight:700;line-height:6.2px;color:var(--navy)}

/* hero */
.hero{left:0;top:0;height:175px;background:linear-gradient(180deg,var(--sky-top) 0%,#cfe0f1 22%,var(--sky-mid) 55%,var(--sky-deep) 100%)}
.hero-title{position:absolute;left:0;right:0;top:56px;text-align:center;font-size:22.5px;font-weight:800;color:var(--white);letter-spacing:.2px}
.hero-copy{position:absolute;left:83px;width:183px;top:88px;text-align:center;font-size:4.3px;line-height:6.1px;color:var(--white)}
.search{position:absolute;left:90px;top:117px;width:170px;height:13px;border-radius:7px;background:var(--white);font-size:4.2px;color:#9a9a9a;display:flex;align-items:center;padding-left:8px}
.search svg{position:absolute;right:6px;top:3.5px}

/* headings */
.section-title{position:absolute;left:0;right:0;text-align:center;font-size:13px;font-weight:600;color:var(--ink);line-height:15px}
.rule{position:absolute;left:50%;width:33px;margin-left:-16.5px;height:1.4px;background:var(--green)}
.intro{position:absolute;left:0;right:0;text-align:center;font-size:4.3px;line-height:6.2px;color:var(--navy)}

/* listing cards */
.band{position:absolute;left:0;width:349px;background:var(--green)}
.card{position:absolute;background:var(--white);border-radius:5px;overflow:hidden;box-shadow:0 1px 3px rgba(0,0,0,.18)}
.photo-lake{background:linear-gradient(180deg,#4f8fd8 0%,#a9cbea 35%,#2f6a2e 55%,#5b8fb8 72%,#4d7a2a 100%)}
.photo-valley{background:linear-gradient(180deg,#b9bdbd 0%,#8e9490 40%,#5d6b4c 70%,#6e6a42 100%)}
.photo-couple{background:linear-gradient(160deg,#3a2f26 0%,#4b4a30 45%,#5d6b3a 75%,#3f4a26 100%)}
.card-photo{position:absolute;left:0;top:0;width:100%}
.card-title{position:absolute;left:6px;font-weight:700;color:var(--navy)}
.card-price{position:absolute;left:6px;font-weight:700;color:var(--green)}
.card-facts{position:absolute;left:6px;font-size:4.3px;line-height:6.2px;color:var(--navy)}
.card-facts b{font-weight:700}
.card-button{position:absolute;left:0;bottom:0;width:100%;background:var(--blue);color:var(--white);font-weight:700;display:flex;align-items:center;justify-content:center;gap:4px}

/* buttons + fields */
.btn{position:absolute;height:15px;border-radius:8px;color:var(--white);font-weight:600;font-size:5px;display:flex;align-items:center;padding-left:9px;background:var(--green)}
.btn svg{position:absolute;right:9px;top:5px}
.btn-blue{background:var(--blue)}
.field{position:absolute;height:18px;background:var(--white);border-radius:9px;box-shadow:0 1px 2px rgba(0,0,0,.14);font-size:5px;display:flex;align-items:center;padding-left:10px;color:var(--ink)}
.field svg{position:absolute;right:9px;top:7px}
.field-area{align-items:flex-start;padding-top:7px;border-radius:7px}
.photo-block{position:absolute;border-radius:6px}
.map{position:absolute;border-radius:5px;background:var(--map-block);box-shadow:0 1px 3px rgba(0,0,0,.15)}

/* contact block */
.loc-title{position:absolute;left:196px;font-size:7.5px;font-weight:600;color:var(--ink)}
.loc-text{position:absolute;left:196px;font-size:5px;line-height:8.8px;color:var(--muted)}
.loc-phone{position:absolute;left:196px;font-size:7px;font-weight:600;color:var(--ink)}

/* footer */
.footer{background:var(--footer)}
.footer-badge{position:absolute;left:154px;top:-14px;width:41px;height:41px;border-radius:50%;background:var(--white);display:flex;align-items:center;justify-content:center;text-align:center;font-size:4.3px;font-weight:700;line-height:5px;color:var(--navy);padding:4px}
.footer-lead{position:absolute;left:0;right:0;top:32px;text-align:center;font-size:5.3px;font-weight:600;color:var(--white)}
.footer-input{position:absolute;left:115px;top:43px;width:119px;height:12px;border-radius:6px;background:var(--white);font-size:3.6px;color:#8a8a8a;display:flex;align-items:center;padding-left:8px}
.footer-input span.go{position:absolute;right:5px;top:3px;width:6px;height:6px;border-radius:50%;border:.6px solid #9a9a9a}
.footer-links{position:absolute;left:0;right:0;top:66px;text-align:center;font-size:4.3px;color:#e6e6e6}
.footer-legal{position:absolute;left:0;right:0;top:77px;text-align:center;font-size:3.6px;color:#e6e6e6;display:flex;justify-content:center;align-items:center;gap:2px}
.social{display:inline-block;width:5px;height:5px;border-radius:50%;background:var(--white);margin-left:2px}

/* detail page */
.detail-header{left:0;top:0;height:22px;background:var(--white);box-shadow:0 1px 2px rgba(0,0,0,.12);z-index:2}
.crumbs{position:absolute;left:0;right:0;top:36px;text-align:center;font-size:3.5px;color:var(--muted)}
.info-card{position:absolute;left:203px;top:108px;width:114px;height:248px;background:var(--white);border-radius:6px;box-shadow:0 1px 3px rgba(0,0,0,.1)}
.info-label{position:absolute;left:9px;font-size:5.5px;font-weight:700;color:var(--navy)}
.info-value{position:absolute;left:9px;font-size:5.5px;color:var(--navy)}
.agent-card{position:absolute;left:29px;top:274px;width:165px;height:82px;background:var(--white);border-radius:6px;box-shadow:0 1px 3px rgba(0,0,0,.1)}
.agent-text{position:absolute;left:65px;font-size:5.7px;line-height:7px;color:var(--navy)}
</style>
</head>
<body>

<main class="page home">
  <header class="section hero">
    <div class="brand"><span class="brand-dot"></span><span class="brand-name">Quiet Hollow Properties</span></div>
    <nav class="nav"><span>HOME</span><span>ABOUT</span><span>PROPERTIES</span><span>CONTACT</span></nav>
    <h1 class="hero-title">Freedom Awaits</h1>
    <p class="hero-copy">Lorem ipsum dolor sit amet, consectetur adipiscing elit. Ut mollis vestibulum odio, ac pellentesque arcu posuere et. Aenean dignissim leo eu ipsum mattis, ac viverra ante malesuada. Nulla eu lacinia elit. Etiam vitae iaculis nunc.</p>
    <div class="search">Find your Quiet Hollow property...
      <svg width="6" height="6" viewBox="0 0 6 6"><circle cx="2.5" cy="2.5" r="1.9" fill="none" stroke="#9a9a9a" stroke-width=".6"/><line x1="3.9" y1="3.9" x2="5.6" y2="5.6" stroke="#9a9a9a" stroke-width=".6"/></svg>
    </div>
  </header>

  <section class="section" style="top:175px;height:275px">
    <h2 class="section-title" style="top:32px">Featured Listings</h2>
    <div class="rule" style="top:51px"></div>
    <p class="intro" style="top:60px">Lorem ipsum dolor sit amet, consectetur adipiscing elit.<br>Ut mollis vestibulum odio, ac pellentesque arcu posuere.</p>
    <div class="band" style="top:115px;height:54px"></div>

    <article class="card" style="left:44px;top:86px;width:81px;height:128px">
      <div class="card-photo photo-lake" style="height:54px" role="img" aria-label="Lake framed by pine forest under a cloudy sky"></div>
      <h3 class="card-title" style="top:58px;font-size:7px;line-height:8px">Mountain Lakeside<br>Private Property</h3>
      <p class="card-price" style="top:76px;font-size:8.5px">$299,999</p>
      <p class="card-facts" style="top:88px"><b>Lot Size:</b> 1.3 Acres<br><b>Address:</b> Street Name,<br>City, State, Zip</p>
      <div class="card-button" style="height:16px;font-size:6px">View Listing <svg width="4" height="5" viewBox="0 0 4 5"><polyline points="1,.5 3,2.5 1,4.5" fill="none" stroke="#fff" stroke-width=".7"/></svg></div>
    </article>
    <article class="card" style="left:134px;top:86px;width:81px;height:128px">
      <div class="card-photo photo-valley" style="height:54px" role="img" aria-label="Misty mountain valley with grassland"></div>
      <h3 class="card-title" style="top:58px;font-size:7px;line-height:8px">Rural Countryside<br>Five Acre Property</h3>
      <p class="card-price" style="top:76px;font-size:8.5px">$299,999</p>
      <p class="card-facts" style="top:88px"><b>Lot Size:</b> 1.3 Acres<br><b>Address:</b> Street Name,<br>City, State, Zip</p>
      <div class="card-button" style="height:16px;font-size:6px">View Listing <svg width="4" height="5" viewBox="0 0 4 5"><polyline points="1,.5 3,2.5 1,4.5" fill="none" stroke="#fff" stroke-width=".7"/></svg></div>
    </article>
    <article class="card" style="left:224px;top:86px;width:81px;height:128px">
      <div class="card-photo photo-lake" style="height:54px" role="img" aria-label="Lake framed by pine forest under a cloudy sky"></div>
      <h3 class="card-title" style="top:58px;font-size:7px;line-height:8px">Mountain Lakeside<br>Private Property</h3>
      <p class="card-price" style="top:76px;font-size:8.5px">$299,999</p>
      <p class="card-facts" style="top:88px"><b>Lot Size:</b> 1.3 Acres<br><b>Address:</b> Street Name,<br>City, State, Zip</p>
      <div class="card-button" style="height:16px;font-size:6px">View Listing <svg width="4" height="5" viewBox="0 0 4 5"><polyline points="1,.5 3,2.5 1,4.5" fill="none" stroke="#fff" stroke-width=".7"/></svg></div>
    </article>

    <div class="btn" style="left:129px;top:228px;width:91px">Or Browse All Listings
      <svg width="4" height="5" viewBox="0 0 4 5"><polyline points="1,.5 3,2.5 1,4.5" fill="none" stroke="#fff" stroke-width=".7"/></svg></div>
  </section>

  <section class="section panel" style="top:450px;height:210px">
    <h2 class="section-title" style="top:24px">Find a Property</h2>
    <div class="rule" style="top:44px"></div>
    <p class="intro" style="top:52px">Lorem ipsum dolor sit amet, consectetur adipiscing elit.<br>Ut mollis vestibulum odio, ac pellentesque arcu posuere.</p>
    <div class="photo-block photo-couple" style="left:41px;top:77px;width:118px;height:95px" role="img" aria-label="Couple walking across a grassy field toward a wooden cabin"></div>
    <div class="field" style="left:166px;top:77px;width:142px">Keywords...</div>
    <div class="field" style="left:166px;top:103px;width:142px">City, State or Zip</div>
    <div class="field" style="left:166px;top:129px;width:67px">Lot Size<svg width="7" height="4" viewBox="0 0 7 4"><polyline points=".5,.5 3.5,3.3 6.5,.5" fill="none" stroke="#888" stroke-width=".6"/></svg></div>
    <div class="field" style="left:241px;top:129px;width:67px">Price Range<svg width="7" height="4" viewBox="0 0 7 4"><polyline points=".5,.5 3.5,3.3 6.5,.5" fill="none" stroke="#888" stroke-width=".6"/></svg></div>
    <div class="btn" style="left:166px;top:155px;width:92px">Find Your Property<svg width="4" height="5" viewBox="0 0 4 5"><polyline points="1,.5 3,2.5 1,4.5" fill="none" stroke="#fff" stroke-width=".7"/></svg></div>
  </section>

  <section class="section" style="top:660px;height:250px">
    <h2 class="section-title" style="top:22px">Get in Touch</h2>
    <div class="rule" style="top:42px"></div>
    <div class="field" style="left:41px;top:64px;width:67px">First Name</div>
    <div class="field" style="left:116px;top:64px;width:67px">Last Name</div>
    <div class="field" style="left:41px;top:90px;width:142px">Email Address</div>
    <div class="field" style="left:41px;top:116px;width:142px">Subject<svg width="7" height="4" viewBox="0 0 7 4"><polyline points=".5,.5 3.5,3.3 6.5,.5" fill="none" stroke="#888" stroke-width=".6"/></svg></div>
    <div class="field field-area" style="left:41px;top:143px;width:142px;height:48px">Tell us what you are looking for...</div>
    <div class="btn" style="left:41px;top:198px;width:92px">Find Your Property<svg width="4" height="5" viewBox="0 0 4 5"><polyline points="1,.5 3,2.5 1,4.5" fill="none" stroke="#fff" stroke-width=".7"/></svg></div>
    <h3 class="loc-title" style="top:63px">Location</h3>
    <p class="loc-text" style="top:73px">Street Address Street Address<br>City, State Zip</p>
    <p class="loc-phone" style="top:97px">555-555-5555</p>
    <div class="map" style="left:195px;top:116px;width:113px;height:96px" role="img" aria-label="Map of the office location"></div>
  </section>

  <footer class="section footer" style="top:910px;height:98px">
    <div class="footer-badge">Quiet Hollow Properties</div>
    <p class="footer-lead">Sign Up for to Hear About New Listings</p>
    <div class="footer-input">Enter your email address<span class="go"></span></div>
    <p class="footer-links">Properties &nbsp;|&nbsp; Features &nbsp;|&nbsp; Agents &nbsp;|&nbsp; Contact</p>
    <p class="footer-legal">© 2022 Quiet Hollow Properties &nbsp;|&nbsp; Terms of Service &nbsp;|&nbsp; Privacy Notice <span class="social"></span><span class="social"></span></p>
  </footer>
</main>

<main class="page detail">
  <header class="section detail-header">
    <div class="brand"><span class="brand-dot"></span><span class="brand-name">Quiet Hollow Properties</span></div>
    <nav class="nav"><span>HOME</span><span>ABOUT</span><span>PROPERTIES</span><span>CONTACT</span></nav>
  </header>

  <section class="section panel" style="top:0;height:378px">
    <p class="crumbs">Home/Properties/Mountain Lakeside Private Property</p>
    <h1 class="section-title" style="top:56px">Mountain Lakeside<br>Private Property</h1>
    <div class="rule" style="top:91px"></div>

    <div class="photo-block photo-lake" style="left:29px;top:108px;width:165px;height:114px;border-radius:2px" role="img" aria-label="Main photo of the lakeside property with pine forest"></div>
    <div class="photo-block photo-lake" style="left:29px;top:225px;width:39px;height:27px;border-radius:1px" role="img" aria-label="Gallery thumbnail of the lake"></div>
    <div class="photo-block photo-lake" style="left:71px;top:225px;width:39px;height:27px;border-radius:1px" role="img" aria-label="Gallery thumbnail of the lake"></div>
    <div class="photo-block photo-lake" style="left:113px;top:225px;width:39px;height:27px;border-radius:1px" role="img" aria-label="Gallery thumbnail of the lake"></div>
    <div class="photo-block photo-lake" style="left:155px;top:225px;width:39px;height:27px;border-radius:1px" role="img" aria-label="Gallery thumbnail of the lake"></div>

    <p class="abs" style="left:29px;width:165px;top:261px;text-align:center;font-size:7px;color:var(--ink)">Listing Agent</p>
    <div class="agent-card">
      <div class="abs" style="left:9px;top:7px;width:50px;height:50px;border-radius:50%;background:linear-gradient(160deg,#e8e4e0,#c9b8ae)" role="img" aria-label="Portrait of the listing agent"></div>
      <p class="agent-text" style="top:10px"><b>Name</b><br>Phone Number<br>Email Address</p>
      <p class="agent-text" style="top:38px">Street Name<br>City, State Zip</p>
      <div class="btn" style="left:9px;top:62px;width:71px;height:14px;font-size:4.6px">Contact Agent<svg width="4" height="5" viewBox="0 0 4 5"><polyline points="1,.5 3,2.5 1,4.5" fill="none" stroke="#fff" stroke-width=".7"/></svg></div>
      <div class="btn btn-blue" style="left:84px;top:62px;width:71px;height:14px;font-size:4.6px">Schedule a Tour<svg width="4" height="5" viewBox="0 0 4 5"><polyline points="1,.5 3,2.5 1,4.5" fill="none" stroke="#fff" stroke-width=".7"/></svg></div>
    </div>

    <aside class="info-card">
      <p class="abs" style="left:9px;top:6px;font-size:11.5px;font-weight:700;color:var(--green)">$299,999</p>
      <p class="info-label" style="top:26px">Lot Size:</p>
      <p class="info-value" style="top:33px">1.3 Acres</p>
      <p class="info-label" style="top:47px">Details:</p>
      <p class="abs" style="left:9px;top:56px;width:98px;font-size:4.2px;line-height:6.2px;color:var(--navy)">Lorem ipsum dolor sit amet, consectetur adipiscing elit. Aliquam eleifend sodales placerat. Etiam ligula sapien, blandit non purus id, sodales laoreet mi. In vitae dui eu nisl vestibulum pharetra ut a ligula. Integer eget cursus ligula, a elementum nibh. Quisque id pretium purus. Nunc id vehicula nunc. Proin a tellus id eros viverra sodales ut id lorem. Nulla eget ante sed dui gravida suscipit a et turpis. Mauris pellentesque feugiat tellus, a eleifend ante mattis et.</p>
      <p class="info-label" style="top:138px">Address:</p>
      <p class="info-value" style="top:145px">Street Name, City, State, Zip</p>
      <div class="map" style="left:8px;top:158px;width:99px;height:80px;border-radius:2px" role="img" aria-label="Map of the property location"></div>
    </aside>
  </section>

  <section class="section" style="top:378px;height:173px">
    <h2 class="section-title" style="top:25px">Similar Listings</h2>
    <div class="rule" style="top:45px"></div>
    <div class="band" style="top:81px;height:33px"></div>
    <article class="card" style="left:31px;top:65px;width:66px;height:78px">
      <div class="card-photo photo-lake" style="height:34px" role="img" aria-label="Lake framed by pine forest"></div>
      <h3 class="card-title" style="top:38px;font-size:5.1px;line-height:6.2px;left:5px">Mountain Lakeside<br>Private Property</h3>
      <p class="card-price" style="top:52px;font-size:6.6px;left:5px">$299,999</p>
      <div class="card-button" style="height:12px;font-size:4.6px">View Listing <svg width="4" height="5" viewBox="0 0 4 5"><polyline points="1,.5 3,2.5 1,4.5" fill="none" stroke="#fff" stroke-width=".7"/></svg></div>
    </article>
    <article class="card" style="left:106px;top:65px;width:66px;height:78px">
      <div class="card-photo photo-lake" style="height:34px" role="img" aria-label="Lake framed by pine forest"></div>
      <h3 class="card-title" style="top:38px;font-size:5.1px;line-height:6.2px;left:5px">Mountain Lakeside<br>Private Property</h3>
      <p class="card-price" style="top:52px;font-size:6.6px;left:5px">$299,999</p>
      <div class="card-button" style="height:12px;font-size:4.6px">View Listing <svg width="4" height="5" viewBox="0 0 4 5"><polyline points="1,.5 3,2.5 1,4.5" fill="none" stroke="#fff" stroke-width=".7"/></svg></div>
    </article>
    <article class="card" style="left:181px;top:65px;width:66px;height:78px">
      <div class="card-photo photo-lake" style="height:34px" role="img" aria-label="Lake framed by pine forest"></div>
      <h3 class="card-title" style="top:38px;font-size:5.1px;line-height:6.2px;left:5px">Mountain Lakeside<br>Private Property</h3>
      <p class="card-price" style="top:52px;font-size:6.6px;left:5px">$299,999</p>
      <div class="card-button" style="height:12px;font-size:4.6px">View Listing <svg width="4" height="5" viewBox="0 0 4 5"><polyline points="1,.5 3,2.5 1,4.5" fill="none" stroke="#fff" stroke-width=".7"/></svg></div>
    </article>
    <article class="card" style="left:257px;top:65px;width:66px;height:78px">
      <div class="card-photo photo-lake" style="height:34px" role="img" aria-label="Lake framed by pine forest"></div>
      <h3 class="card-title" style="top:38px;font-size:5.1px;line-height:6.2px;left:5px">Mountain Lakeside<br>Private Property</h3>
      <p class="card-price" style="top:52px;font-size:6.6px;left:5px">$299,999</p>
      <div class="card-button" style="height:12px;font-size:4.6px">View Listing <svg width="4" height="5" viewBox="0 0 4 5"><polyline points="1,.5 3,2.5 1,4.5" fill="none" stroke="#fff" stroke-width=".7"/></svg></div>
    </article>
  </section>

  <section class="section panel" style="top:551px;height:210px">
    <h2 class="section-title" style="top:24px">Find a Property</h2>
    <div class="rule" style="top:44px"></div>
    <p class="intro" style="top:52px">Lorem ipsum dolor sit amet, consectetur adipiscing elit.<br>Ut mollis vestibulum odio, ac pellentesque arcu posuere.</p>
    <div class="photo-block photo-couple" style="left:41px;top:77px;width:118px;height:95px" role="img" aria-label="Couple walking across a grassy field toward a wooden cabin"></div>
    <div class="field" style="left:166px;top:77px;width:142px">Keywords...</div>
    <div class="field" style="left:166px;top:103px;width:142px">City, State or Zip</div>
    <div class="field" style="left:166px;top:129px;width:67px">Lot Size<svg width="7" height="4" viewBox="0 0 7 4"><polyline points=".5,.5 3.5,3.3 6.5,.5" fill="none" stroke="#888" stroke-width=".6"/></svg></div>
    <div class="field" style="left:241px;top:129px;width:67px">Price Range<svg width="7" height="4" viewBox="0 0 7 4"><polyline points=".5,.5 3.5,3.3 6.5,.5" fill="none" stroke="#888" stroke-width=".6"/></svg></div>
    <div class="btn" style="left:166px;top:155px;width:92px">Find Your Property<svg width="4" height="5" viewBox="0 0 4 5"><polyline points="1,.5 3,2.5 1,4.5" fill="none" stroke="#fff" stroke-width=".7"/></svg></div>
  </section>

  <section class="section" style="top:761px;height:250px">
    <h2 class="section-title" style="top:22px">Get in Touch</h2>
    <div class="rule" style="top:42px"></div>
    <div class="field" style="left:41px;top:64px;width:67px">First Name</div>
    <div class="field" style="left:116px;top:64px;width:67px">Last Name</div>
    <div class="field" style="left:41px;top:90px;width:142px">Email Address</div>
    <div class="field" style="left:41px;top:116px;width:142px">Subject<svg width="7" height="4" viewBox="0 0 7 4"><polyline points=".5,.5 3.5,3.3 6.5,.5" fill="none" stroke="#888" stroke-width=".6"/></svg></div>
    <div class="field field-area" style="left:41px;top:143px;width:142px;height:48px">Tell us what you are looking for...</div>
    <div class="btn" style="left:41px;top:198px;width:92px">Find Your Property<svg width="4" height="5" viewBox="0 0 4 5"><polyline points="1,.5 3,2.5 1,4.5" fill="none" stroke="#fff" stroke-width=".7"/></svg></div>
    <h3 class="loc-title" style="top:63px">Location</h3>
    <p class="loc-text" style="top:73px">Street Address Street Address<br>City, State Zip</p>
    <p class="loc-phone" style="top:97px">555-555-5555</p>
    <div class="map" style="left:195px;top:116px;width:113px;height:96px" role="img" aria-label="Map of the office location"></div>
  </section>

  <footer class="section footer" style="top:1011px;height:98px">
    <div class="footer-badge">Quiet Hollow Properties</div>
    <p class="footer-lead">Sign Up for to Hear About New Listings</p>
    <div class="footer-input">Enter your email address<span class="go"></span></div>
    <p class="footer-links">Properties &nbsp;|&nbsp; Features &nbsp;|&nbsp; Agents &nbsp;|&nbsp; Contact</p>
    <p class="footer-legal">© 2022 Quiet Hollow Properties &nbsp;|&nbsp; Terms of Service &nbsp;|&nbsp; Privacy Notice <span class="social"></span><span class="social"></span></p>
  </footer>
</main>

</body>
</html>
```